Corvana - Waste to Fuel Power Needs A Website

Make website explaining the concept and the team behind the company
Updates

I will be providing A logo and Information about the company upon signed NDA.

Coding

Coded - Design and coding required

Number of Pages Required

5+ page

```html
<!DOCTYPE html>
<html lang="en">
<head>
<meta charset="utf-8">
<title>Corvana - Waste to Fuel Power</title>
<link href="https://fonts.googleapis.com/css2?family=Outfit:wght@400;500;600;700;800&display=swap" rel="stylesheet">
<style>
:root{
  --orange:#f7860f;
  --green:#4a8c3f;
  --green-dark:#3f7d36;
  --ink:#161616;
  --text:#555;
  --line:#dedede;
  --black:#151515;
  --white:#fff;
}
*{box-sizing:border-box;margin:0;padding:0}
html,body{width:1200px;height:3774px;overflow:hidden}
body{font-family:'Outfit',sans-serif;color:var(--ink);background:var(--white);position:relative}
.abs{position:absolute}
h1,h2,h3{font-weight:700;letter-spacing:-0.5px}
.btn{display:inline-block;background:var(--orange);color:#fff;font-size:13px;font-weight:500;border-radius:5px;padding:0 19px;line-height:40px;text-decoration:none}
.btn.green{background:var(--green)}
/* top bar */
.topbar{left:0;top:0;width:1200px;height:37px;background:var(--black);color:#fff;font-size:12px;text-align:center;line-height:37px;border-radius:0 0 18px 18px}
.nav{left:113px;top:37px;width:974px;height:86px;display:flex;align-items:center;justify-content:space-between}
.brand{font-size:34px;font-weight:800;color:var(--green);line-height:1}
.brand small{display:block;font-size:11px;color:var(--orange);font-weight:600;letter-spacing:.5px;margin-top:2px}
.menu{display:flex;align-items:center;gap:32px;font-size:13px;color:#333}
.menu .btn{margin-left:-8px;line-height:44px;padding:0 22px}
/* hero */
.hero{left:0;top:123px;width:1200px;height:592px;border-radius:20px;overflow:hidden;background:linear-gradient(100deg,#4a4c4e 0%,#6b747c 45%,#8fa2b3 70%,#6f7f5e 100%)}
.hero-copy{left:113px;top:135px;width:500px;color:#fff}
.hero-copy h1{font-size:53px;line-height:60px}
.hero-copy p{font-size:12px;line-height:19px;margin:14px 0 18px;width:460px}
.hero-copy .btn{margin-right:4px}
/* section titles */
.sec-title{width:1200px;text-align:center;font-size:34px;left:0}
.sec-sub{width:1200px;left:0;text-align:center;font-size:12px;line-height:19px;color:var(--text)}
/* why cards */
.card{width:227px;height:167px;border:1.5px solid var(--line);border-radius:14px;text-align:center;padding-top:22px}
.icon{width:54px;height:54px;border-radius:8px;margin:0 auto 14px;display:flex;align-items:center;justify-content:center}
.icon.g{background:var(--green)}.icon.o{background:var(--orange)}
.card h3{font-size:16px;font-weight:600}
.card p{font-size:11.5px;color:var(--text);line-height:18px;margin:6px auto 0;width:180px}
/* world */
.photo{border-radius:16px}
.world-copy{left:640px;top:1160px;width:400px}
.world-copy h2{font-size:34px;line-height:42px}
.world-copy p{font-size:11.5px;line-height:19px;color:var(--text);margin-top:14px}
.world-copy h4{font-size:13px;font-weight:600;margin:16px 0 12px}
.bullets{list-style:none;font-size:11.5px;color:var(--text)}
.bullets li{position:relative;padding-left:16px;margin-bottom:13px}
.bullets li::before{content:"";position:absolute;left:0;top:4px;width:8px;height:8px;border-radius:50%;background:var(--orange)}
/* solution */
.solution{left:0;top:1528px;width:1200px;height:507px;background:var(--green);border-radius:20px}
.solution h2{color:#fff;text-align:center;font-size:34px;line-height:42px;margin-top:62px}
.solution p{color:#fff;text-align:center;font-size:11.5px;margin-top:12px}
.steps-row{display:flex;gap:18px;margin:18px 0 0 122px}
.sol-item{width:226px;text-align:center;color:#fff}
.sol-item .photo{height:180px;border:2px solid #fff;border-radius:12px}
.sol-item span{display:block;font-size:14px;font-weight:600;line-height:21px;margin-top:10px}
/* serving */
.serve-copy{left:173px;top:2153px;width:360px}
.serve-copy h2{font-size:34px;line-height:42px}
.serve-copy p{font-size:11.5px;line-height:19px;color:var(--text);margin:12px 0 14px}
.serve-copy .bullets li{margin-bottom:12px}
/* cleaner */
.dash{top:2677px;left:370px;width:460px;border-top:1.5px dashed #ccc}
.step{width:160px;text-align:center}
.step b{display:block;width:60px;height:60px;margin:0 auto;border-radius:7px;color:#fff;font-size:26px;font-weight:500;line-height:60px}
.step span{display:block;font-size:13px;font-weight:500;line-height:20px;margin-top:18px}
/* team */
.team-card{width:227px;height:197px;border-radius:12px;border:1.5px solid #eee}
/* footer */
.footer{left:0;top:3506px;width:1200px;height:268px;background:var(--black);border-radius:20px 20px 0 0;color:#fff}
.f-brand{position:absolute;left:113px;top:80px;font-size:44px;font-weight:800;line-height:1}
.f-brand small{display:block;font-size:15px;font-weight:500;letter-spacing:.5px;margin-top:6px}
.f-nav{position:absolute;left:567px;top:90px;width:520px;display:flex;justify-content:flex-end;gap:31px;font-size:12px}
.f-line{position:absolute;left:567px;top:121px;width:520px;border-top:1px solid #444}
.f-contact{position:absolute;left:612px;top:139px;width:475px;display:flex;align-items:center;font-size:12px;gap:8px}
.f-social{margin-left:auto;display:flex;gap:22px}
.f-social i{width:12px;height:12px;border-radius:50%;background:#fff;display:block}
.f-bottom{position:absolute;left:113px;top:215px;width:974px;border-top:1px solid #444}
.f-copy{position:absolute;left:0;top:235px;width:1200px;text-align:center;font-size:12px}
</style>
</head>
<body>
<div class="abs topbar">Business Diesel Supply Partnerships Commercial Inquiries</div>
<header class="abs nav">
  <div class="brand">Corvana<small>WASTE TO FUEL POWER</small></div>
  <nav class="menu"><span>Home</span><span>About</span><span>Technology</span><span>Environmental Impact</span><span>Team</span><span>Contact</span><a class="btn">Get Commercial Supply</a></nav>
</header>

<section class="abs hero" role="img" aria-label="Fuel tanker truck on an open highway under a cloudy sky"></section>
<div class="abs hero-copy">
  <h1>Turning Plastic Waste Into Valuable Diesel Fuel</h1>
  <p>Corvana transforms plastic waste into high-quality diesel through advanced conversion technology. We help industries power their operations.</p>
  <a class="btn">Learn About Our Technology</a><a class="btn green">Request Diesel Supply</a>
</div>

<h2 class="abs sec-title" style="top:782px">Why Corvana Matters</h2>
<div class="abs card" style="left:117px;top:850px"><div class="icon g"><svg width="28" height="28" fill="none" stroke="#fff" stroke-width="2"><circle cx="14" cy="14" r="10"/><path d="M4 14h20M14 4c4 4 4 16 0 20M14 4c-4 4-4 16 0 20"/></svg></div><h3>Environmental Impact</h3><p>We reduce plastic pollution by converting waste.</p></div>
<div class="abs card" style="left:363px;top:850px"><div class="icon o"><svg width="28" height="28" fill="none" stroke="#fff" stroke-width="2"><path d="M22 10a9 9 0 1 0 1 7M22 4v6h-6"/></svg></div><h3>Circular Economy</h3><p>Waste becomes resource instead of a landfill problem.</p></div>
<div class="abs card" style="left:609px;top:850px"><div class="icon o"><svg width="28" height="28" fill="none" stroke="#fff" stroke-width="2"><circle cx="14" cy="14" r="10"/><path d="M14 8v12M17 10h-4a2 2 0 0 0 0 4h2a2 2 0 0 1 0 4h-4"/></svg></div><h3>Cost Efficiency</h3><p>Industries gain access to alternative diesel fuel solutions.</p></div>
<div class="abs card" style="left:855px;top:850px"><div class="icon g"><svg width="28" height="28" fill="none" stroke="#fff" stroke-width="2"><path d="M7 24V6h10v18zM17 10l4 3v8a2 2 0 0 0 2 0V12M9 10h6"/></svg></div><h3>Reliable Diesel Supply</h3><p>We provide consistent diesel supply for commercial.</p></div>

<div class="abs photo" style="left:195px;top:1110px;width:401px;height:327px;background:linear-gradient(160deg,#9fb6cf,#7d7561 60%,#4e4a3e)" role="img" aria-label="Two volunteers collecting plastic waste on a lakeshore"></div>
<div class="abs world-copy">
  <h2>The World Has<br>Too Much Plastic Waste</h2>
  <p>Every year millions of tons of plastic end up in landfills and oceans.<br>At the same time, industries depend heavily on diesel fuel to operate.</p>
  <h4>This creates two major global challenges:</h4>
  <ul class="bullets"><li>Growing plastic pollution.</li><li>Rising demand for industrial fuel.</li></ul>
</div>

<section class="abs solution">
  <h2>Our Solution:<br>Plastic to Diesel Technology</h2>
  <p>Corvana uses advanced thermal conversion technology to break down plastic waste &amp; convert it into usable diesel fuel.</p>
  <div class="steps-row">
    <div class="sol-item"><div class="photo" style="background:linear-gradient(135deg,#3a4d5c,#a7b3b9)" role="img" aria-label="Worker in protective suit beside steel reactor tanks"></div><span>Plastic is processed in a controlled thermal reactor</span></div>
    <div class="sol-item"><div class="photo" style="background:linear-gradient(135deg,#6f7a6a,#b9a9a0)" role="img" aria-label="People collecting and sorting plastic waste"></div><span>Plastic waste is collected and sorted</span></div>
    <div class="sol-item"><div class="photo" style="background:linear-gradient(135deg,#5e6b63,#c79a3a)" role="img" aria-label="Person filling a fuel canister at a pump"></div><span>High-quality diesel fuel is produced</span></div>
    <div class="sol-item"><div class="photo" style="background:linear-gradient(180deg,#2b3440,#7d858c 60%,#3f8a3a)" role="img" aria-label="Refinery towers releasing vapor"></div><span>Hydrocarbon vapors are captured &amp; refined</span></div>
  </div>
</section>

<div class="abs serve-copy">
  <h2>Serving Commercial<br>Diesel Buyers</h2>
  <p>Corvana focuses on supplying diesel fuel to industries that rely heavily on commercial fuel consumption.</p>
  <ul class="bullets"><li>Logistics &amp; Trucking Companies.</li><li>Construction Companies.</li><li>Industrial Manufacturing Plants.</li><li>Power Generation Facilities.</li><li>Large Fleet Operators.</li></ul>
</div>
<div class="abs photo" style="left:626px;top:2126px;width:401px;height:326px;background:linear-gradient(150deg,#2f4f8a,#8a8f92 55%,#9a4d3a)" role="img" aria-label="Two workers in safety vests walking past trucks and containers"></div>

<h2 class="abs sec-title" style="top:2535px">Cleaner Energy. Cleaner Planet.</h2>
<p class="abs sec-sub" style="top:2585px">By converting plastic waste into diesel fuel, Corvana helps reduce landfill waste &amp; creates<br>a more sustainable energy cycle.</p>
<div class="abs dash"></div>
<div class="abs step" style="left:256px;top:2647px"><b style="background:var(--green)">01</b><span>Reduce global plastic<br>pollution</span></div>
<div class="abs step" style="left:519px;top:2647px"><b style="background:var(--orange)">02</b><span>Provide alternative<br>diesel fuel</span></div>
<div class="abs step" style="left:786px;top:2647px"><b style="background:var(--green)">03</b><span>Support industrial<br>sustainability</span></div>

<h2 class="abs sec-title" style="top:2840px">The Team Behind Corvana</h2>
<p class="abs sec-sub" style="top:2890px">Corvana was founded by engineers, environmental innovators, and energy specialists<br>who share a common mission:</p>
<div class="abs team-card" style="left:117px;top:2983px;background:#edf3ec" role="img" aria-label="Team member in hard hat and high-visibility vest"></div>
<div class="abs team-card" style="left:363px;top:2983px;background:#fcf0e4" role="img" aria-label="Team member in hard hat and plaid shirt"></div>
<div class="abs team-card" style="left:609px;top:2983px;background:#edf3ec" role="img" aria-label="Team member in hard hat and tool belt"></div>
<div class="abs team-card" style="left:855px;top:2983px;background:#fcf0e4" role="img" aria-label="Team member in hard hat and overalls"></div>

<h2 class="abs sec-title" style="top:3265px;font-size:40px">Looking for Commercial Diesel Supply?</h2>
<p class="abs sec-sub" style="top:3325px">Partner with Corvana to secure reliable diesel fuel while contributing to a cleaner environment.</p>
<a class="abs btn" style="left:523px;top:3361px;width:154px;text-align:center;padding:0">Request Partnership</a>

<footer class="abs footer">
  <div class="f-brand">Corvana<small>WASTE TO FUEL POWER</small></div>
  <nav class="f-nav"><span>Home</span><span>About</span><span>Technology</span><span>Environmental Impact</span><span>Team</span><span>Contact</span></nav>
  <div class="f-line"></div>
  <div class="f-contact">
    <svg width="12" height="12" viewBox="0 0 24 24" fill="var(--orange)"><path d="M6.6 10.8a15 15 0 0 0 6.6 6.6l2.2-2.2a1 1 0 0 1 1-.3 11 11 0 0 0 3.6.6 1 1 0 0 1 1 1V20a1 1 0 0 1-1 1A17 17 0 0 1 3 4a1 1 0 0 1 1-1h3.5a1 1 0 0 1 1 1 11 11 0 0 0 .6 3.6 1 1 0 0 1-.3 1z"/></svg>
    <span>+100 (555) 0199</span>
    <svg style="margin-left:110px" width="12" height="12" viewBox="0 0 24 24" fill="var(--orange)"><path d="M2 5h20v14H2zm2 2v.5l8 5 8-5V7z"/></svg>
    <span>info@corvana.com</span>
    <div class="f-social"><i></i><i></i><i></i><i></i></div>
  </div>
  <div class="f-bottom"></div>
  <div class="f-copy">© 2026 Corvana. All rights reserved.</div>
</footer>
</body>
</html>
```